Boutique Real Estate Brokerage Tessly Realty Website Design

Winning designer work on migrate as well through nest ferry.
We need a new website as an informational hub to aid our print and digital strategy as well as showing that we are located in Brooklyn and Florida. I have a boutique real estate brokerage and advisory firm specializing in residential leasing, multifamily sales and 1031 Exchange appropriation. This won't be a portal to search properties, it will be a place for information. I'd like space for an ebook to be downloaded and information on my probate sales and multifamily leasing marketing campaigns. I included my logo and will leave it up to the designer to come up with colors to match it. I have also attached verbiage for each page. The final design should have a modern high end look that reflects gentrifying Brooklyn as well as beautiful Florida.
Thank you!
Target Market(s)
Owners of income producing real estate and develop-able land in Brooklyn, NY and Florida.
Industry/Entity Type
Real Estate
Coding
Coded - Design and coding required
Number of Pages Required
5+ page
Colors
Designer to choose colors to be used in the design.
Requirements
Must have
- A modern elegant look
Nice to have
- pictures of brooklyn and florida
Should not have
- real estate search pages

```html
<!DOCTYPE html>
<html lang="en">
<head>
<meta charset="utf-8">
<title>Tessly Realty</title>
<link href="https://fonts.googleapis.com/css2?family=Montserrat:wght@400;500;600;700&family=Mulish:wght@400;600&display=swap" rel="stylesheet">
<style>
:root{
  --black:#000;
  --ink:#1a1a1a;
  --heading:#3d3d3d;
  --heading-soft:#8a8a8a;
  --body:#6b6b6b;
  --light-bg:#efefef;
  --band-bg:#e8e7e9;
  --white:#fff;
  --line:#cfcfcf;
  --hero-a:#6e5a3c;
  --hero-b:#8c6a3a;
  --dark-a:#2b2521;
  --dark-b:#3b3430;
}
*{box-sizing:border-box;margin:0;padding:0}
html,body{width:1200px;height:3432px;overflow:hidden}
body{position:relative;font-family:'Mulish',Arial,sans-serif;color:var(--body);background:var(--white)}
.abs{position:absolute}
.heading{font-family:'Montserrat',sans-serif;font-weight:600;color:var(--heading)}
.heading .soft{color:var(--heading-soft)}
.btn{position:absolute;background:var(--black);color:var(--white);font-family:'Montserrat',sans-serif;font-weight:500;font-size:19px;border-radius:5px;display:flex;align-items:center;justify-content:center;letter-spacing:.2px}

/* header */
.site-header{left:0;top:0;width:1200px;height:93px;background:var(--black)}
.brand{left:77px;top:30px;display:flex;align-items:center;gap:12px;font-family:'Montserrat',sans-serif;font-weight:600;color:#cfcfcf;font-size:15px;letter-spacing:2.5px;text-transform:uppercase}
.brand-mark{width:30px;height:30px;border-radius:50%;background:#bdbdbd}
.nav{left:0;top:0;width:1200px;height:93px;font-family:'Montserrat',sans-serif;font-size:14px;color:#d8d8d8}
.nav-item{position:absolute;top:37px}
.nav-active{position:absolute;left:663px;top:27px;width:84px;height:40px;border:1px solid #fff;border-radius:5px;color:#fff;display:flex;align-items:center;justify-content:center}

/* hero */
.hero{left:0;top:93px;width:1200px;height:562px;background:linear-gradient(180deg,#8a7a5c 0%,var(--hero-a) 45%,var(--hero-b) 100%)}
.hero-title{left:0;top:318px;width:1200px;text-align:center;font-family:'Montserrat',sans-serif;font-weight:700;font-size:37px;line-height:47px;color:var(--white);text-transform:uppercase;text-shadow:0 2px 6px rgba(0,0,0,.4)}
.hero .btn{}
.hero-btn{left:503px;top:436px;width:194px;height:57px;font-size:20px}

/* help section */
.help{left:0;top:655px;width:1200px;height:714px;background:var(--light-bg)}
.help-title{left:0;top:758px;width:1200px;text-align:center;font-size:42px}
.card{position:absolute;top:833px;width:313px;height:468px;background:var(--white)}
.card-photo{position:absolute;left:0;top:0;width:313px;height:218px}
.card-title{position:absolute;left:27px;top:250px;font-family:'Montserrat',sans-serif;font-weight:600;font-size:18px;color:var(--ink)}
.card-text{position:absolute;left:28px;top:288px;width:270px;font-size:13.5px;line-height:26px;color:var(--body)}
.card .btn{left:29px;top:386px;width:161px;height:52px}

/* welcome */
.welcome-kicker{left:121px;top:1446px;font-size:21px}
.welcome-title{left:119px;top:1478px;font-size:41px}
.welcome-text{left:122px;top:1543px;width:410px;font-size:13.5px;line-height:27px}
.welcome-text p{margin-bottom:16px}
.welcome-btn{left:123px;top:1796px;width:161px;height:52px}
.welcome-art{left:639px;top:1439px;width:465px;height:416px}

/* call band */
.call-band{left:0;top:1910px;width:1200px;height:261px;background:linear-gradient(90deg,var(--dark-a),var(--dark-b) 50%,#2e2824)}
.call-title{left:0;top:1986px;width:1200px;text-align:center;font-family:'Montserrat',sans-serif;font-weight:600;font-size:28px;color:var(--white)}
.call-btn{left:473px;top:2045px;width:254px;height:58px;border:1.5px solid #fff;border-radius:7px;display:flex;align-items:center;justify-content:center;gap:14px;font-family:'Montserrat',sans-serif;font-weight:600;font-size:25px;color:var(--white)}

/* contact */
.contact-title{left:0;top:2230px;width:1200px;text-align:center;font-size:42px}
.contact-sub{left:0;top:2287px;width:1200px;text-align:center;font-size:15px;color:var(--body)}
.field{position:absolute;left:326px;width:548px;border-bottom:1px solid var(--line);font-family:Arial,sans-serif;font-size:12.5px;color:#777;padding-left:2px}
.submit-btn{left:527px;top:2607px;width:146px;height:52px;font-weight:600}

/* ebook */
.ebook-band{left:0;top:2780px;width:1200px;height:324px;background:var(--band-bg)}
.ebook-cover{left:166px;top:2691px;width:247px;height:359px;background:linear-gradient(100deg,#111 0%,#1c1c1c 60%,#0a0a0a 100%);display:flex;align-items:flex-end;justify-content:center;padding-bottom:100px;color:#fff;font-family:'Montserrat',sans-serif;font-size:40px;font-weight:400}
.ebook-title{left:446px;top:2838px;font-size:40px}
.ebook-lead{left:446px;top:2903px;font-family:Arial,sans-serif;font-size:18px;color:#222}
.ebook-note{left:446px;top:2934px;font-family:Arial,sans-serif;font-size:15px;color:#555}
.ebook-input{left:446px;top:2970px;width:484px;height:56px;background:var(--white);border-radius:4px;font-family:Arial,sans-serif;font-size:14px;color:#555;display:flex;align-items:center;padding-left:15px}
.ebook-btn{left:939px;top:2970px;width:177px;height:56px;font-weight:600}

/* footer */
.site-footer{left:0;top:3104px;width:1200px;height:328px;background:linear-gradient(90deg,#2c2a28,#3a3634 50%,#2d2a28)}
.footer-brand{left:0;top:3186px;width:1200px;text-align:center;font-family:'Montserrat',sans-serif;font-weight:600;font-size:22px;letter-spacing:3px;color:#cfcfcf;text-transform:uppercase}
.social{position:absolute;top:3274px;width:46px;height:46px;border:1.5px solid #fff;border-radius:50%}
.footer-links{left:0;top:3337px;width:1200px;text-align:center;font-size:13.5px;color:#c9c9c9}
.footer-copy{left:0;top:3362px;width:1200px;text-align:center;font-size:13.5px;color:#bdbdbd}
.footer-copy b{color:#fff;font-weight:600}
</style>
</head>
<body>

<header class="abs site-header">
  <div class="abs brand"><span class="brand-mark"></span>Tessly Realty</div>
  <nav class="abs nav">
    <span class="nav-active">HOME</span>
    <span class="nav-item" style="left:779px">ABOUT US</span>
    <span class="nav-item" style="left:884px">SERVICES</span>
    <span class="nav-item" style="left:982px">CONTACT US</span>
    <svg class="nav-item" style="left:1107px;top:38px" width="14" height="14" viewBox="0 0 14 14"><circle cx="5.5" cy="5.5" r="4" fill="none" stroke="#fff" stroke-width="2"/><line x1="8.5" y1="8.5" x2="13" y2="13" stroke="#fff" stroke-width="2.2"/></svg>
  </nav>
</header>

<section class="abs hero" role="img" aria-label="Warm sepia photo of a Brooklyn bridge walkway with steel cables"></section>
<h1 class="abs hero-title">Assisting landlords increase profits<br>while decreasing the stress.</h1>
<div class="btn hero-btn">CONTACT US</div>

<section class="abs help"></section>
<svg class="abs" style="left:0;top:654px" width="1200" height="46" viewBox="0 0 1200 46">
  <path d="M480 0 C540 0 555 44 600 44 C645 44 660 0 720 0 Z" fill="#8c6a3a"/>
</svg>
<svg class="abs" style="left:577px;top:651px" width="46" height="24" viewBox="0 0 46 24">
  <g fill="#fff"><circle cx="3" cy="2" r="1.2"/><circle cx="9" cy="2" r="1.2"/><circle cx="15" cy="2" r="1.2"/><circle cx="21" cy="2" r="1.2"/><circle cx="27" cy="2" r="1.2"/><circle cx="33" cy="2" r="1.2"/><circle cx="39" cy="2" r="1.2"/><circle cx="43" cy="2" r="1.2"/>
  <circle cx="8" cy="8" r="1.2"/><circle cx="14" cy="8" r="1.2"/><circle cx="20" cy="8" r="1.2"/><circle cx="26" cy="8" r="1.2"/><circle cx="32" cy="8" r="1.2"/><circle cx="38" cy="8" r="1.2"/>
  <circle cx="14" cy="14" r="1.2"/><circle cx="20" cy="14" r="1.2"/><circle cx="26" cy="14" r="1.2"/><circle cx="32" cy="14" r="1.2"/>
  <circle cx="20" cy="20" r="1.2"/><circle cx="26" cy="20" r="1.2"/></g>
</svg>
<h2 class="abs heading help-title">HOW <span class="soft">WE CAN</span> HELP</h2>

<article class="card" style="left:97px">
  <div class="card-photo" role="img" aria-label="Bright apartment kitchen and dining room interior" style="background:linear-gradient(135deg,#d9d6cf,#9c9790 60%,#6c655c)"></div>
  <h3 class="card-title">MULTI-FAMILY LEASING</h3>
  <p class="card-text">We specialize in sourcing quality tenants for landlords with high income, good credit and no evictions.</p>
  <div class="btn">LEARN MORE</div>
</article>
<article class="card" style="left:444px">
  <div class="card-photo" role="img" aria-label="Brick multifamily building facade with fire escapes" style="background:linear-gradient(180deg,#8e9396,#7a6e62 40%,#4a4038)"></div>
  <h3 class="card-title" style="left:25px">MULTIFAMILY SALES</h3>
  <p class="card-text" style="left:26px">Tessly Realty provides clients with reliable real estate research, advisory and transaction services.</p>
  <div class="btn" style="left:27px">LEARN MORE</div>
</article>
<article class="card" style="left:790px">
  <div class="card-photo" role="img" aria-label="Aerial view of Florida land and waterfront" style="background:linear-gradient(180deg,#aab2b8 0%,#7d8a7c 35%,#5c6b4e 70%,#3d4a3a 100%)"></div>
  <h3 class="card-title" style="left:30px">SITE SELECTION ADVISORS</h3>
  <p class="card-text" style="left:31px">Our industry best Commercial Real Estate site selection services assists developers in narrow.</p>
  <div class="btn" style="left:32px">LEARN MORE</div>
</article>

<p class="abs heading welcome-kicker">WEL<span class="soft">COME</span> TO</p>
<h2 class="abs heading welcome-title">TESS<span class="soft">LY REAL</span>TY</h2>
<div class="abs welcome-text">
  <p>Tessly Realty NYC•PB is a full-service real estate brokerage firm with offices located in Brooklyn, New York and West Palm Beach, Florida. Our firm focuses on multifamily leasing, sales and Commercial Real Estate Site Selection Advisory</p>
  <p>Our clients are private and institutional multifamily real estate investors.Our team differentiates ourselves by our ability to investigate the highest and best use for real estate assets as well as our high deal closing rate.</p>
</div>
<div class="btn welcome-btn">LEARN MORE</div>
<svg class="abs welcome-art" viewBox="0 0 465 416" role="img" aria-label="Two businessmen reviewing documents at a desk">
  <path d="M40 60 C110 -10 300 -10 390 50 C470 110 480 230 420 300 C360 370 230 410 120 390 C20 370 -15 250 5 170 C15 120 20 80 40 60 Z" fill="#e3f0fb"/>
  <path d="M60 70 C120 10 300 0 390 60 C450 110 460 230 410 290 C350 360 240 400 140 395 C50 390 10 290 10 200 C10 140 30 100 60 70 Z" fill="#b7aa9b"/>
</svg>

<section class="abs call-band" role="img" aria-label="Dark photo of a Brooklyn brownstone entrance"></section>
<p class="abs call-title">If You have an an Any Question For Contact Us On</p>
<div class="abs call-btn">
  <svg width="30" height="30" viewBox="0 0 30 30"><circle cx="15" cy="15" r="13" fill="none" stroke="#fff" stroke-width="1.6"/><path d="M11 8 L13.5 11 L12 13 C13 15.5 14.5 17 17 18 L19 16.5 L22 19 L20 21.5 C14 21.5 8.5 16 8.5 10 Z" fill="none" stroke="#fff" stroke-width="1.5" stroke-linejoin="round"/></svg>
  555 014 2290
</div>

<h2 class="abs heading contact-title">CONTA<span class="soft">CT</span> US</h2>
<p class="abs contact-sub">If you want more info or just to say hello !</p>
<div class="field" style="top:2351px;height:25px">Name *</div>
<div class="field" style="top:2401px;height:31px">Email *</div>
<div class="field" style="top:2458px;height:30px">Phone *</div>
<div class="field" style="top:2510px;height:82px">Message *</div>
<div class="btn submit-btn">SUBMIT</div>

<section class="abs ebook-band"></section>
<div class="abs ebook-cover" role="img" aria-label="Black e-book box cover">E-BOOK</div>
<h2 class="abs heading ebook-title">DOWNL<span class="soft">OAD</span> E-BOOK</h2>
<p class="abs ebook-lead">Free Download in exchange for business information.</p>
<p class="abs ebook-note">Enter your email to get access to my free E-BOOK.</p>
<div class="abs ebook-input">Enter Your Email*</div>
<div class="btn ebook-btn">SUBSCRIBE</div>

<footer class="abs site-footer" role="img" aria-label="Dark photo of a smiling team of professionals"></footer>
<p class="abs footer-brand">Tessly Realty</p>
<span class="social" style="left:524px"></span>
<span class="social" style="left:577px"></span>
<span class="social" style="left:630px"></span>
<p class="abs footer-links">Home &nbsp;|&nbsp; About Us | &nbsp;Services &nbsp;|&nbsp; Contact Us</p>
<p class="abs footer-copy">©<b>TESSLY REALTY</b> - 2019 All Right Reserved.</p>

</body>
</html>
```